High end Electrical/home automation Business Card

Need a card for a high end electrical and home automation company utilising the existing logo.
Phone
Email
Website

Like black look with raised detail. Don’t necessarily need to keep colour of logo it could be made grayscale or white etc

Target Market(s)

High end clients

Contact Information for Business Card

Brightmoor Electrical

Requirements
Must have
• Logo, phone, email, website, address

High end look
Nice to have
• Black background card
Raised font
Should not have
• Lots of colour

```html
<!DOCTYPE html>
<html lang="en">
<head>
<meta charset="utf-8">
<title>Brightmoor Electrical — Business Card</title>
<link href="https://fonts.googleapis.com/css2?family=Arimo:wght@400;700&display=swap" rel="stylesheet">
<style>
  :root {
    --backdrop: #9c9c9c;
    --card: #222223;
    --ink: #ffffff;
    --accent: #2196d6;
  }
  * { box-sizing: border-box; margin: 0; padding: 0; }
  html, body {
    width: 1021px;
    height: 1200px;
    overflow: hidden;
    background: var(--backdrop);
    font-family: "Arimo", Arial, sans-serif;
    color: var(--ink);
  }
  .card {
    position: absolute;
    width: 753px;
    height: 429px;
    background: var(--card);
  }
  .card--front { left: 134px; top: 119px; }
  .card--back  { left: 131px; top: 651px; }

  .brand-name {
    font-weight: 700;
    color: var(--ink);
    letter-spacing: -0.5px;
    white-space: nowrap;
  }
  .card--front .brand-name {
    position: absolute;
    right: 35px;
    top: 346px;
    font-size: 40px;
  }
  .card--back .brand {
    position: absolute;
    left: 0; right: 0;
    top: 76px;
    display: flex;
    flex-direction: column;
    align-items: center;
    gap: 18px;
  }
  .brand-dot {
    width: 64px; height: 64px;
    border-radius: 50%;
    background: var(--accent);
  }
  .card--back .brand-name { font-size: 29px; }

  .person {
    position: absolute;
    right: calc(753px - 350px);
    top: 265px;
    text-align: right;
  }
  .person-name {
    font-weight: 700;
    font-size: 30px;
    color: var(--accent);
    letter-spacing: 0.5px;
    line-height: 1;
  }
  .person-role {
    font-size: 18px;
    margin-top: 4px;
  }
  .divider {
    position: absolute;
    left: 375px;
    top: 261px;
    width: 2px;
    height: 61px;
    background: var(--accent);
  }
  .contacts {
    position: absolute;
    left: 409px;
    top: 255px;
    list-style: none;
    font-size: 18.5px;
    line-height: 24.5px;
  }
  .contacts li { display: flex; align-items: center; gap: 8px; }
  .contacts svg { width: 14px; height: 14px; flex: none; }
  .contacts .accent { color: var(--accent); }

  .address-band {
    position: absolute;
    left: 0; right: 0;
    top: 359px;
    height: 37px;
    background: var(--accent);
    display: flex;
    align-items: center;
    justify-content: center;
    font-size: 17px;
  }
</style>
</head>
<body>

<section class="card card--front" aria-label="Card front">
  <p class="brand-name">Brightmoor Electrical</p>
</section>

<section class="card card--back" aria-label="Card back">
  <div class="brand">
    <span class="brand-dot"></span>
    <p class="brand-name">Brightmoor Electrical</p>
  </div>

  <div class="person">
    <p class="person-name">DANIEL HARTLEY</p>
    <p class="person-role">Co-Founder</p>
  </div>

  <span class="divider"></span>

  <ul class="contacts">
    <li>
      <svg viewBox="0 0 24 24" fill="#2196d6" aria-hidden="true"><path d="M6.6 10.8a15.1 15.1 0 0 0 6.6 6.6l2.2-2.2a1 1 0 0 1 1-.25 11.4 11.4 0 0 0 3.6.57 1 1 0 0 1 1 1V20a1 1 0 0 1-1 1A17 17 0 0 1 3 4a1 1 0 0 1 1-1h3.5a1 1 0 0 1 1 1c0 1.25.2 2.46.57 3.6a1 1 0 0 1-.25 1z"/></svg>
      <span>555-014-2286</span>
    </li>
    <li>
      <svg viewBox="0 0 24 24" fill="#2196d6" aria-hidden="true"><path d="M2 5h20v14H2z M4 7v.4l8 5.6 8-5.6V7l-8 5.6z" fill-rule="evenodd"/></svg>
      <span>daniel@brightmoorelectrical.com</span>
    </li>
    <li>
      <svg viewBox="0 0 24 24" fill="none" stroke="#2196d6" stroke-width="2" aria-hidden="true"><circle cx="12" cy="12" r="9"/><path d="M3 12h18M12 3c3 3 3 15 0 18M12 3c-3 3-3 15 0 18"/></svg>
      <span>www.<span class="accent">brightmoorelectrical</span>.com</span>
    </li>
  </ul>

  <p class="address-band">2180 Alder Creek Rd Suite C Ashford.</p>
</section>

</body>
</html>
```